project - Misto Den

Dear designers, I'm Looking for an appealing new business card design to represent us for our new e-cigarette store: The MistO Den. Knowledgeable and friendly staff we aim for superior customer service with a positive atmosphere. Classic feel with modern touch is what we are aiming for . Lime green font and grey back round is the original color scheme but we are flexible and open to suggestions. I added some doodles to show you where my mind is at. address: 4827 203 St SW Edmonton, AB (inside the grand swap bazaar)web: themistoden.com email: info@themistoden.com phone : 555.214.6093 Thanks and am looking forward to seeing your creative , fresh and innovative designs.
Good luck everybody!
Gordon
Updates
lime green and charcoal grey please. thanks
Industry/Entity Type
Business
Logo Text
The MistO Den
Look and feel
Each slider illustrates characteristics of the customer's brand and the style your logo design should communicate.

```html
<!DOCTYPE html>
<html lang="en">
<head>
<meta charset="utf-8">
<title>The MistO Den – Business Card</title>
<link href="https://fonts.googleapis.com/css2?family=Exo+2:wght@400;500;600;800&display=swap" rel="stylesheet">
<style>
  :root {
    --lime: #3da636;
    --lime-light: #8fd04b;
    --lime-dark: #22852f;
    --charcoal: #3b3d40;
    --grey-text: #6a6d70;
    --card-white: #ffffff;
    --card-shade: #e9eaeb;
    --backdrop: #d9d9d6;
  }
  * { box-sizing: border-box; margin: 0; padding: 0; }
  html, body { width: 1200px; height: 828px; overflow: hidden; }
  body {
    background: var(--backdrop);
    font-family: "Exo 2", Arial, sans-serif;
    position: relative;
  }
  .card {
    position: absolute;
    top: 260px;
    width: 540px;
    height: 309px;
    background: linear-gradient(160deg, var(--card-white) 30%, var(--card-shade) 100%);
    box-shadow: 0 6px 18px rgba(0,0,0,0.18);
    overflow: hidden;
  }
  .card--front { left: 40px; }
  .card--back { left: 620px; }

  .wordmark {
    font-weight: 800;
    color: var(--lime);
    text-transform: uppercase;
    letter-spacing: -1px;
    line-height: 0.9;
  }
  .card--front .wordmark {
    position: absolute;
    left: 0; right: 0;
    top: 88px;
    text-align: center;
    font-size: 76px;
  }
  .card--back .wordmark {
    position: absolute;
    left: 26px;
    top: 108px;
    font-size: 56px;
    white-space: nowrap;
  }

  .holder {
    position: absolute;
    right: 26px;
    top: 30px;
    text-align: left;
    width: 150px;
  }
  .holder__name {
    color: var(--lime);
    font-size: 11px;
    font-weight: 600;
    letter-spacing: 0.8px;
    text-transform: uppercase;
  }
  .holder__role {
    color: var(--grey-text);
    font-size: 8.5px;
    margin-top: 2px;
  }
  .holder__address {
    color: var(--grey-text);
    font-size: 9px;
    line-height: 1.5;
    margin-top: 16px;
  }

  .contact-list {
    position: absolute;
    left: 30px;
    top: 198px;
    list-style: none;
  }
  .contact-list li {
    display: flex;
    align-items: center;
    gap: 7px;
    font-size: 9.5px;
    color: var(--charcoal);
    height: 16px;
  }
  .contact-list svg { width: 10px; height: 10px; fill: var(--lime); flex: none; }

  .swoosh { position: absolute; left: 0; top: 0; width: 540px; height: 309px; }
  .swoosh__url {
    font-family: "Exo 2", Arial, sans-serif;
    font-size: 11px;
    font-weight: 500;
    fill: #ffffff;
    letter-spacing: 0.6px;
  }
</style>
</head>
<body>

  <section class="card card--front" aria-label="Card front">
    <div class="wordmark">Misto<br>Den</div>
  </section>

  <section class="card card--back" aria-label="Card back">
    <svg class="swoosh" viewBox="0 0 540 309" aria-hidden="true">
      <defs>
        <linearGradient id="swoosh-fill" x1="0" y1="1" x2="1" y2="0">
          <stop offset="0" stop-color="var(--lime-dark)"/>
          <stop offset="1" stop-color="var(--lime-light)"/>
        </linearGradient>
        <path id="url-path" d="M318,302 C390,268 462,236 540,214"/>
      </defs>
      <path d="M190,309 C300,250 420,195 540,160" fill="none" stroke="#4a4c4f" stroke-width="4"/>
      <path d="M215,309 C320,252 430,200 540,172 L540,309 Z" fill="url(#swoosh-fill)"/>
      <text class="swoosh__url"><textPath href="#url-path">www.themistoden.com</textPath></text>
    </svg>

    <div class="holder">
      <p class="holder__name">Gordon Reyes</p>
      <p class="holder__role">Managing Director</p>
      <p class="holder__address">4827 203 St SW<br>Edmonton, AB</p>
    </div>

    <div class="wordmark">Misto Den</div>

    <ul class="contact-list">
      <li>
        <svg viewBox="0 0 10 10"><path d="M2 0.5 L3.6 0.5 L4.2 2.8 L3 3.6 C3.6 5 5 6.4 6.4 7 L7.2 5.8 L9.5 6.4 L9.5 8 C9.5 9 8.6 9.6 7.6 9.4 C4.4 8.7 1.3 5.6 0.6 2.4 C0.4 1.4 1 0.5 2 0.5 Z"/></svg>
        555.214.6093
      </li>
      <li>
        <svg viewBox="0 0 10 10"><path d="M2.5 0 H7.5 V10 H2.5 Z M3.3 1 V8 H6.7 V1 Z"/></svg>
        555.214.6093
      </li>
      <li>
        <svg viewBox="0 0 10 10"><path d="M2.5 0 H7.5 V3 H2.5 Z M0.5 3.5 H9.5 V7.5 H8 V6 H2 V7.5 H0.5 Z M2.5 6.5 H7.5 V10 H2.5 Z"/></svg>
        555.214.6093
      </li>
      <li>
        <svg viewBox="0 0 10 10"><path d="M0 1.5 H10 V8.5 H0 Z M0.8 2.2 L5 5.4 L9.2 2.2 Z"/></svg>
        info@themistoden.com
      </li>
    </ul>
  </section>

</body>
</html>
```